Doctor Formulated Medical Cosmetics

Velour Skinhaus is an E-commerce site for high end Medical Cosmetics designed to treat specific skin problems. The Velour Skinhaus difference/advantage is that all creams and serums are:
Doctor Formulated, Freshly Handmade, Registered Pharmacy.
The Site also provides real doctor Dermatology Consultations, Library (with a list of - 1. Active Ingredients in the creams with description of their effects, 2. Skin Conditions with information on what causes the condition and typical treatment approaches and outcomes. 3. Resources from Dermatology Journals and literature on the conditions.)
Header Information: Velour Skinhaus, languages EN, BG, Register / log in, Shopping Bag. This field should be narrow.
Categories (horizontal): Home, Face, Body, Hair Care, Skin Conditions, Doctor Consultation, Library
The Landing Page should have only one well organized picture, which is intended to create the feeling of luxury, freedom and relaxation. It will be large and will fill the whole screen. All text should be on transparent or similar color fields. Please use the color of the text to create also the feeling of conservative luxury.
Written message / image overlay Velour Skinhaus(logo), Skin Care, Doctor Formulated, Freshly Handmade, Registered Pharmacy.
Please study the Landing Page of this site as an example: www.marivane.com
Under the Landing Page, there should be a slider with 4 of our products.
Underneath: Four Blog Articles (large pictures for maximum impact and luxury text underneath).
Underneath: Banner for Dermatologist Consultation, (button for Start Your Case Now).
Underneath: Two pictures in a line - Library (with books), and Active Ingredients.
Footer: Philosophy, Categories, Customer Care
Please adhere to the color palate provided in the pictures (as attachments). Provided are some examples of Web Sites with the desired look and feel. www.quillora.com , www.tavenholtmd.com .
Please use different shades of gray, white, beige and gold colors, and black. Our products will be in brown glass jars and bottles to convey the professional, pharmacy made nature of the creams and lotions.
We find the following Front Page very attractive and effective - www.marivane.com , with its full page image and overlaying text.
Please have a look at this link for the Landing page.
http://www.brimlensphoto.com/detail/video/woman-lying-on-a-black-sand-beach-in-a-bikini-stock-footage/58213067
I would like to use it in the animated version to achieve the WOW effect. I have uploaded the jpeg version for it, so you will be able create your design.
For the Landing page design, please use only the two uploaded pictures of a woman laying at the beach. Let's see how each of them will look like.
Thank you for your help.

```html
<!DOCTYPE html>
<html lang="en">
<head>
<meta charset="utf-8">
<title>Velour Skinhaus — Doctor Formulated Medical Cosmetics</title>
<link href="https://fonts.googleapis.com/css2?family=Lato:wght@300;400;700&family=Lora:ital,wght@0,400;1,400&display=swap" rel="stylesheet">
<style>
:root{
  --gold:#c9a45c;
  --gold-dark:#b38d45;
  --ink:#2a2a2a;
  --text:#3c3c3c;
  --line:#dccaa0;
  --header-top:#3b3b3b;
  --header-bot:#1e1e1e;
  --footer:#1f1f1f;
  --footer-bar:#141414;
  --white:#fff;
}
*{box-sizing:border-box;margin:0;padding:0}
html,body{width:1200px;height:2416px;overflow:hidden;background:var(--white)}
body{position:relative;font-family:'Lato',sans-serif;color:var(--text)}

/* header */
.site-header{position:absolute;left:0;top:0;width:1200px;height:105px;background:linear-gradient(var(--header-top),var(--header-bot));border-bottom:3px solid var(--gold);z-index:2}
.brand{position:absolute;left:58px;top:28px;display:flex;align-items:center;gap:12px;color:var(--gold);font-family:'Lora',serif;font-size:33px}
.brand-dot{width:14px;height:14px;border:2px solid var(--gold);border-radius:50%}
.utility{position:absolute;left:477px;top:0;width:642px;height:40px;background:#2a2a2a;border-radius:0 0 18px 18px;display:flex;justify-content:space-around;align-items:center;font-size:13px;color:#ddd}
.utility span{display:flex;align-items:center;gap:6px}
.utility svg{width:12px;height:12px;fill:#ddd}
.main-nav{position:absolute;left:382px;top:56px;display:flex;height:46px}
.main-nav a{color:#f2f2f2;text-decoration:none;font-size:14.5px;font-weight:700;padding:10px 18px 0;border-left:1px solid #4a4a4a;height:46px}
.main-nav a:last-child{border-right:1px solid #4a4a4a}
.main-nav a.active{background:#2a2a2a;border-bottom:3px solid #fff}

/* hero */
.hero{position:absolute;left:0;top:105px;width:1200px;height:483px;
  background:
    radial-gradient(ellipse 38% 30% at 55% 62%,rgba(196,132,84,.95),rgba(196,132,84,0) 100%),
    radial-gradient(ellipse 22% 40% at 12% 40%,rgba(214,118,62,.85),rgba(214,118,62,0) 100%),
    radial-gradient(ellipse 25% 45% at 88% 35%,rgba(150,60,40,.55),rgba(150,60,40,0) 100%),
    radial-gradient(ellipse 30% 35% at 70% 20%,rgba(230,228,220,.8),rgba(230,228,220,0) 100%),
    linear-gradient(180deg,#8cb3cf 0%,#6f8f5c 35%,#b3926e 62%,#9c7d62 80%,#2f5f88 92%,#21496d 100%)}
.hero-caption{position:absolute;left:60px;top:180px;width:417px;height:113px;background:rgba(40,30,20,.55);color:#fff;font-family:'Lora',serif;font-style:italic;font-size:27px;line-height:38px;padding:18px 32px}
.dots{position:absolute;left:1078px;top:441px;display:flex;gap:8px}
.dots i{width:15px;height:15px;border:2px solid #fff;border-radius:50%}
.dots i.on{background:var(--gold)}

/* section titles */
.section-title{position:absolute;left:0;width:1200px;text-align:center;font-size:36px;font-weight:400;color:var(--ink);line-height:44px}
.section-title em{font-style:normal;color:var(--gold)}
.rule{position:absolute;left:58px;width:1082px;height:1px;background:var(--line)}
.rule::after{content:"";position:absolute;left:531px;top:0;border:10px solid transparent;border-top:8px solid #333;border-bottom:0}

/* products */
.products-deco{position:absolute;left:1000px;top:588px;width:200px;height:434px;background:radial-gradient(ellipse 70% 50% at 80% 50%,#d6dcae,#eef0dc 55%,#fff 100%)}
.product{position:absolute;top:700px;width:185px;height:279px;border:1px solid #e2e2e2;background:#fff;text-align:center}
.product .shot{position:absolute;left:29px;top:14px;width:127px;height:160px;background:radial-gradient(ellipse 42% 50% at 50% 52%,#7a421a,#b36f32 45%,#e9d3bd 78%,#fff 100%)}
.product .shot.dark{background:radial-gradient(ellipse 38% 50% at 50% 52%,#0e0e0e,#333 50%,#d9d9d9 80%,#fff 100%)}
.product p{position:absolute;top:192px;width:100%;font-size:14px;line-height:21px;color:#333}
.product .price{position:absolute;left:32px;top:243px;font-weight:700;font-size:15px;color:#222}
.cart-btn{position:absolute;left:113px;top:236px;width:34px;height:34px;border-radius:50%;background:var(--gold);display:flex;align-items:center;justify-content:center}
.cart-btn svg{width:18px;height:18px;fill:#fff}
.arrow{position:absolute;top:789px;width:37px;height:53px;display:flex;align-items:center;justify-content:center}
.arrow svg{width:22px;height:22px;stroke:#fff;stroke-width:2.5;fill:none}

/* consultation */
.consult{position:absolute;left:0;top:1022px;width:1200px;height:461px;background:linear-gradient(90deg,#e2e5e6,#eceeef 50%,#dfe3e2)}
.consult-photo{position:absolute;left:0;top:0;width:520px;height:461px;background:
  radial-gradient(ellipse 30% 45% at 25% 30%,rgba(196,160,110,.75),rgba(196,160,110,0) 100%),
  radial-gradient(ellipse 35% 60% at 70% 70%,rgba(250,250,250,.95),rgba(250,250,250,0) 100%),
  linear-gradient(90deg,#8b9096 0%,#c9c4bc 40%,#ecebe8 80%,rgba(236,238,239,0) 100%)}
.consult h2{position:absolute;left:518px;top:92px;font-size:42px;font-weight:400;color:#1e1e1e;line-height:52px}
.consult p{position:absolute;left:518px;top:166px;width:580px;font-size:15.5px;line-height:31.5px;color:#333}
.call-btn{position:absolute;left:523px;top:306px;width:258px;height:55px;background:var(--gold);border-radius:3px;color:#fff;font-size:21px;display:flex;align-items:center;gap:22px;padding-left:14px;box-shadow:0 2px 4px rgba(0,0,0,.2)}
.call-btn .ic{width:40px;height:36px;border-right:1px solid rgba(255,255,255,.6);display:flex;align-items:center}
.call-btn svg{width:26px;height:26px;fill:#fff}
.consult-products{position:absolute;left:890px;top:1262px;width:280px;height:270px;background:radial-gradient(ellipse 48% 48% at 50% 52%,#9a9a9a,#c4c4c4 45%,rgba(220,222,223,.6) 70%,rgba(236,238,239,0) 100%)}

/* articles */
.article{position:absolute;width:495px;height:176px;border:1px solid #ddd;background:#fff}
.article .pic{position:absolute;left:0;top:0;width:166px;height:174px}
.article h3{position:absolute;left:186px;top:18px;font-size:19px;font-weight:700;color:var(--gold);letter-spacing:.3px}
.article p{position:absolute;left:186px;top:52px;width:290px;font-size:14px;line-height:20.5px;color:#333}
.read-more{position:absolute;left:187px;top:124px;width:106px;height:29px;background:var(--gold);color:#fff;font-size:12px;font-weight:700;display:flex;align-items:center;justify-content:center}

/* newsletter */
.newsletter{position:absolute;left:0;top:2056px;width:1200px;height:78px;background:var(--gold)}
.mail-ic{position:absolute;left:95px;top:12px;width:56px;height:56px;border-radius:50%;background:#fff;border:3px solid #333;display:flex;align-items:center;justify-content:center}
.mail-ic svg{width:26px;height:26px;fill:none;stroke:#333;stroke-width:2}
.newsletter h4{position:absolute;left:177px;top:13px;color:#fff;font-size:21px;font-weight:400}
.newsletter small{position:absolute;left:177px;top:43px;color:#fff;font-size:14px;font-style:italic}
.email-field{position:absolute;left:541px;top:17px;width:428px;height:44px;border:1px solid #fff;color:#fff;font-size:12px;font-style:italic;padding:13px 14px}
.subscribe{position:absolute;left:989px;top:17px;width:120px;height:44px;background:#fff;color:#222;font-size:13px;font-weight:700;display:flex;align-items:center;justify-content:center}

/* footer */
.site-footer{position:absolute;left:0;top:2134px;width:1200px;height:234px;background:var(--footer);color:#eee}
.col-title{position:absolute;top:28px;font-size:17px;color:#fff}
.col-rule{position:absolute;top:62px;height:1px;background:#666}
.philosophy{position:absolute;left:61px;top:77px;width:352px;font-size:13.5px;line-height:19.7px;text-align:justify;color:#ddd}
.links{position:absolute;top:80px;list-style:none;font-size:14px;line-height:26.5px;color:#ddd}
.links li::before{content:"›";color:var(--gold);margin-right:6px}
.contact-row{position:absolute;left:899px;display:flex;gap:12px;font-size:13px;color:#ddd;line-height:18px}
.contact-row svg{width:16px;height:16px;fill:var(--gold);flex:none;margin-top:2px}
.contact-row b{color:#fff}
.footer-bar{position:absolute;left:0;top:2368px;width:1200px;height:48px;background:var(--footer-bar);color:#ccc;font-size:12px}
.footer-bar .copy{position:absolute;left:58px;top:17px}
.social{position:absolute;left:540px;top:10px;display:flex;gap:6px}
.social i{width:28px;height:28px;border-radius:50%;background:var(--gold)}
.accept{position:absolute;left:852px;top:17px}
.cards{position:absolute;left:929px;top:12px;display:flex;gap:7px}
.cards i{width:37px;height:24px;background:#e8e8e8;border-radius:2px}
</style>
</head>
<body>

<header class="site-header">
  <div class="brand"><span>Velour Skinhaus</span><span class="brand-dot"></span></div>
  <div class="utility">
    <span><svg viewBox="0 0 12 12"><circle cx="6" cy="3.5" r="3"/><path d="M0 12c0-4 3-5 6-5s6 1 6 5z"/></svg>Doctor</span>
    <span><svg viewBox="0 0 12 12"><rect x="1" y="3" width="10" height="8" rx="1"/></svg>Pharmacy</span>
    <span><svg viewBox="0 0 12 12"><rect x="2" y="5" width="8" height="7"/><path d="M4 5V3a2 2 0 0 1 4 0v2" fill="none" stroke="#ddd"/></svg>Register / log in</span>
    <span><svg viewBox="0 0 12 12"><path d="M0 1h2l2 7h7l1-5H3"/><circle cx="5" cy="10.5" r="1.2"/><circle cx="10" cy="10.5" r="1.2"/></svg>Shopping Cart</span>
    <span><svg viewBox="0 0 12 12"><rect x="0" y="2" width="12" height="8" fill="#8a8a8a"/></svg>English ⌄</span>
  </div>
  <nav class="main-nav">
    <a class="active">Home</a><a>Face</a><a>Body</a><a>Hair Care</a><a>Skin Care</a><a>Dermatologist Consultation</a><a>Contact Us</a>
  </nav>
</header>

<section class="hero" role="img" aria-label="Woman in a sun hat relaxing by a poolside under palm trees">
  <div class="hero-caption">Get That Flawless, Glowing Skin In Few Weeks</div>
  <div class="dots"><i></i><i class="on"></i><i></i></div>
</section>

<div class="products-deco" role="img" aria-label="Olive branch and cream jar"></div>
<h2 class="section-title" style="top:617px">Our <em>Products</em></h2>
<div class="rule" style="top:667px"></div>

<div class="arrow" style="left:60px;background:#e2e2e2"><svg viewBox="0 0 24 24"><path d="M19 12H5M11 6l-6 6 6 6"/></svg></div>
<div class="arrow" style="left:1101px;background:#333"><svg viewBox="0 0 24 24"><path d="M5 12h14M13 6l6 6-6 6"/></svg></div>

<div class="product" style="left:116px"><div class="shot" role="img" aria-label="Brown glass cream jar"></div><p>Lorem ipsum dolor<br>sit amet consectetuer</p><span class="price">$375,00</span><span class="cart-btn"><svg viewBox="0 0 12 12"><path d="M0 1h2l2 7h7l1-5H3"/><circle cx="5" cy="10.5" r="1.2"/><circle cx="10" cy="10.5" r="1.2"/></svg></span></div>
<div class="product" style="left:377px"><div class="shot" role="img" aria-label="Amber glass pump bottle"></div><p>Lorem ipsum dolor<br>sit amet consectetuer</p><span class="price">$145,00</span><span class="cart-btn"><svg viewBox="0 0 12 12"><path d="M0 1h2l2 7h7l1-5H3"/><circle cx="5" cy="10.5" r="1.2"/><circle cx="10" cy="10.5" r="1.2"/></svg></span></div>
<div class="product" style="left:638px"><div class="shot dark" role="img" aria-label="Black serum pump bottle"></div><p>Lorem ipsum dolor<br>sit amet consectetuer</p><span class="price">$375,00</span><span class="cart-btn"><svg viewBox="0 0 12 12"><path d="M0 1h2l2 7h7l1-5H3"/><circle cx="5" cy="10.5" r="1.2"/><circle cx="10" cy="10.5" r="1.2"/></svg></span></div>
<div class="product" style="left:899px"><div class="shot" role="img" aria-label="Amber dropper bottle"></div><p>Lorem ipsum dolor<br>sit amet consectetuer</p><span class="price">$375,00</span><span class="cart-btn"><svg viewBox="0 0 12 12"><path d="M0 1h2l2 7h7l1-5H3"/><circle cx="5" cy="10.5" r="1.2"/><circle cx="10" cy="10.5" r="1.2"/></svg></span></div>

<section class="consult">
  <div class="consult-photo" role="img" aria-label="Dermatologist in a white coat talking with a patient"></div>
  <h2>Dermatologist Consultation</h2>
  <p>Lorem ipsum dolor sit amet, consectetuer adipiscing elit, sed diam nonummy nibh euismod tincidunt ut laoreet dolore magna aliquam erat volutpat. Ut wisi enim ad minim veniam, quis nostrud exerci tation ullamcorper suscipit lobortis nisl ut aliquip ex ea commodo consequat.</p>
  <div class="call-btn"><span class="ic"><svg viewBox="0 0 24 24"><path d="M6.6 10.8a15 15 0 0 0 6.6 6.6l2.2-2.2c.3-.3.7-.4 1-.2 1.1.4 2.3.6 3.6.6.6 0 1 .4 1 1V20c0 .6-.4 1-1 1A17 17 0 0 1 3 4c0-.6.4-1 1-1h3.5c.6 0 1 .4 1 1 0 1.3.2 2.5.6 3.6.1.3 0 .7-.2 1z"/></svg></span>CALL US TODAY</div>
</section>
<div class="consult-products" role="img" aria-label="Silver cosmetic bottles and jars with a brush"></div>

<h2 class="section-title" style="top:1522px">Recent <em>Articles</em></h2>
<div class="rule" style="top:1571px"></div>

<article class="article" style="left:58px;top:1612px"><div class="pic" role="img" aria-label="Woman touching her smooth cheek" style="background:radial-gradient(ellipse 50% 55% at 50% 50%,#e6c7ad,#f4ebe3 70%,#fafafa)"></div><h3>Lorem ipsum dolor sit amet</h3><p>Lorem ipsum dolor sit amet, sed dianummy nibh euismod tincidunt ut dolore. Lorem ipsum dolor ipsum dolor sit.</p><span class="read-more">READ MORE</span></article>
<article class="article" style="left:643px;top:1612px"><div class="pic" role="img" aria-label="Woman with long blonde hair" style="background:radial-gradient(ellipse 45% 55% at 55% 55%,#e6c2a2,#c99b63 55%,#8a6238)"></div><h3>Lorem ipsum dolor sit amet</h3><p>Lorem ipsum dolor sit amet, sed dianummy nibh euismod tincidunt ut dolore. Lorem ipsum dolor ipsum dolor sit.</p><span class="read-more">READ MORE</span></article>
<article class="article" style="left:58px;top:1832px"><div class="pic" role="img" aria-label="Body care, woman in white underwear" style="background:radial-gradient(ellipse 55% 60% at 45% 50%,#e9b898,#f3ddd0 60%,#fbf6f2)"></div><h3>Lorem ipsum dolor sit amet</h3><p>Lorem ipsum dolor sit amet, sed dianummy nibh euismod tincidunt ut dolore. Lorem ipsum dolor ipsum dolor sit.</p><span class="read-more">READ MORE</span></article>
<article class="article" style="left:643px;top:1832px"><div class="pic" role="img" aria-label="Smiling woman with dark hair" style="background:radial-gradient(ellipse 45% 50% at 60% 50%,#efd9c8,#c9a389 55%,#4e3a2e)"></div><h3>Lorem ipsum dolor sit amet</h3><p>Lorem ipsum dolor sit amet, sed dianummy nibh euismod tincidunt ut dolore. Lorem ipsum dolor ipsum dolor sit.</p><span class="read-more">READ MORE</span></article>

<section class="newsletter">
  <div class="mail-ic"><svg viewBox="0 0 26 26"><rect x="3" y="6" width="20" height="14"/><path d="M3 6l10 8 10-8"/></svg></div>
  <h4>Join Our Newsletter!</h4>
  <small>Be the first one to know about our new Offers</small>
  <div class="email-field">Enter Your Email Here</div>
  <div class="subscribe">SUBSCRIBE</div>
</section>

<footer class="site-footer">
  <h5 class="col-title" style="left:61px;font-weight:400">Our Philosophy</h5>
  <div class="col-rule" style="left:61px;width:352px"></div>
  <p class="philosophy">Lorem ipsum dolor sit amet, consectetuer adipisemy nibh euismod tincidunt utre magmi aliquam erat volutpat. Ut wisi enim ad minim veniam quis nostrutation ullaeipit lobortisi nisl ut aliquip nibh euismod tincidunt utre magmi aliquam erat volutpat .ipsum dolor sit amet, consectetuer adipisemy nibh euismod tincidunt utreipsum dolor.</p>

  <h5 class="col-title" style="left:485px;font-weight:400">Quick Links</h5>
  <div class="col-rule" style="left:485px;width:345px"></div>
  <ul class="links" style="left:485px"><li>Home</li><li>Face</li><li>Body</li><li>Hair Care</li><li>Skin Concerns</li></ul>
  <ul class="links" style="left:627px"><li>Dermatologist Consultation</li><li>Library</li><li>Contact Us</li><li>Our Doctors</li><li>Customer Care</li></ul>

  <h5 class="col-title" style="left:899px;font-weight:700">Contact Details</h5>
  <div class="col-rule" style="left:899px;width:240px"></div>
  <div class="contact-row" style="top:78px"><svg viewBox="0 0 16 16"><path d="M8 0a5.5 5.5 0 0 0-5.5 5.5C2.5 10 8 16 8 16s5.5-6 5.5-10.5A5.5 5.5 0 0 0 8 0zm0 8a2.5 2.5 0 1 1 0-5 2.5 2.5 0 0 1 0 5z"/></svg><span><b>Velour Skinhaus</b><br>123 PG Duis Aute Irur Dolore<br>Srephenderit Amit In Voluptate</span></div>
  <div class="contact-row" style="top:150px"><svg viewBox="0 0 24 24"><path d="M6.6 10.8a15 15 0 0 0 6.6 6.6l2.2-2.2c.3-.3.7-.4 1-.2 1.1.4 2.3.6 3.6.6.6 0 1 .4 1 1V20c0 .6-.4 1-1 1A17 17 0 0 1 3 4c0-.6.4-1 1-1h3.5c.6 0 1 .4 1 1 0 1.3.2 2.5.6 3.6.1.3 0 .7-.2 1z"/></svg><b>+123-456-789</b></div>
  <div class="contact-row" style="top:194px"><svg viewBox="0 0 16 16"><path d="M0 3h16v10H0z"/></svg><span>info@velourskinhaus.com</span></div>
</footer>

<div class="footer-bar">
  <span class="copy">Copyright © 2016 Velour Skinhaus. All Rights Reserved.</span>
  <div class="social"><i></i><i></i><i></i><i></i></div>
  <span class="accept">We Accept :</span>
  <div class="cards"><i></i><i></i><i></i><i></i><i></i></div>
</div>

</body>
</html>
```